Oil and Gas Exploration and Production company needs a business card design

We need a business card design using our logo and colors in the logo. We want a mainstream design.

```html
<!DOCTYPE html>
<html lang="en">
<head>
<meta charset="utf-8">
<title>Halden Oil &amp; Gas – Business Card</title>
<link href="https://fonts.googleapis.com/css2?family=Roboto+Slab:wght@400;700&family=Rokkitt:wght@700&family=Roboto:wght@400&display=swap" rel="stylesheet">
<style>
  :root {
    --backdrop: #6a4c36;
    --card-dark: #1e1e1f;
    --gold: #c99a2e;
    --ink: #141414;
    --white: #f4f1ea;
  }
  * { margin: 0; padding: 0; box-sizing: border-box; }
  html, body { width: 1200px; height: 960px; overflow: hidden; }
  body { background: var(--backdrop); position: relative; }

  .card {
    position: absolute;
    width: 600px;
    height: 342px;
    box-shadow: 0 3px 8px rgba(0,0,0,0.35);
  }
  .card--contact { left: 315px; top: 113px; background: var(--card-dark); }
  .card--brand { left: 311px; top: 472px; background: var(--gold); }

  .person-name {
    position: absolute; left: 41px; top: 50px;
    font: 700 21px/1 "Roboto Slab", serif;
    color: var(--gold); letter-spacing: 0.5px;
  }
  .person-role {
    position: absolute; left: 41px; top: 77px;
    font: 400 14px/1 "Roboto Slab", serif;
    color: var(--white);
  }
  .address {
    position: absolute; left: 41px; top: 162px;
    font: 400 13px/18px "Roboto Slab", serif;
    color: var(--white);
  }
  .contact-list {
    position: absolute; left: 41px; top: 210px;
    list-style: none;
    font: 400 13px/19.3px "Roboto Slab", serif;
    color: var(--white);
  }
  .contact-list li { display: flex; align-items: center; gap: 8px; }
  .contact-list svg { width: 13px; height: 13px; fill: var(--gold); flex: none; }

  .emblem { position: absolute; left: 378px; top: 130px; }

  .brand-lockup {
    position: absolute; left: 0; right: 0; top: 130px;
    display: flex; justify-content: center; align-items: center; gap: 16px;
  }
  .brand-lockup__dot { width: 34px; height: 34px; border-radius: 50%; background: var(--ink); }
  .brand-name {
    font: 700 58px/1 "Rokkitt", serif;
    color: var(--ink);
  }
  .brand-url {
    position: absolute; left: 0; right: 0; top: 288px;
    text-align: center;
    font: 400 14px/1 "Roboto", sans-serif;
    letter-spacing: 4.2px;
    color: var(--white);
  }
</style>
</head>
<body>

<section class="card card--contact">
  <h1 class="person-name">DANIEL MORROW</h1>
  <p class="person-role">CEO/FOUNDER</p>
  <p class="address">4120 Spruce Ridge Road<br>Fairbanks, Alaska 99701</p>
  <ul class="contact-list">
    <li><svg viewBox="0 0 16 16"><path d="M3 1l3 3-1.5 2a9 9 0 0 0 5.5 5.5L12 10l3 3-2 2C7 15 1 9 1 3z"/></svg>555 210 4836</li>
    <li><svg viewBox="0 0 16 16"><path d="M4 0h8v16H4zM5.5 2v10h5V2zM7 13.5h2V15H7z" fill-rule="evenodd"/></svg>555 318 7702</li>
    <li><svg viewBox="0 0 16 16"><path d="M4 1h8v4H4zM1 6h14v7h-3v2H4v-2H1zM5 11v3h6v-3z" fill-rule="evenodd"/></svg>555 402 1957</li>
    <li><svg viewBox="0 0 16 16"><path d="M1 3h14v10H1zM2 4l6 5 6-5z" fill-rule="evenodd"/></svg>info@haldenoilgas.com</li>
    <li><svg viewBox="0 0 16 16"><circle cx="8" cy="8" r="7"/></svg>www.haldenoilgas.com</li>
  </ul>
  <svg class="emblem" width="90" height="90" viewBox="0 0 90 90" aria-hidden="true">
    <circle cx="45" cy="45" r="45" fill="var(--gold)"/>
  </svg>
</section>

<section class="card card--brand">
  <div class="brand-lockup">
    <span class="brand-lockup__dot"></span>
    <span class="brand-name">Halden Oil &amp; Gas</span>
  </div>
  <p class="brand-url">www.haldenoilgas.com</p>
</section>

</body>
</html>
```